Chimney Service company needs new business card design

We need a updated business card with our new logo added. We provide a full range of chimney services throughout Vermont and New Hampshire. The business card will be one sided and color. Attached is our current business card another document showing all the information we would like on the card.
We dont like a lot of flashy colors.... here is a link to our website to get an idea of our branding www.flueguardianvt.example

Target Market(s)

homeowners

Industry/Entity Type

Business

Contact Information for Business Card

See attached sheet for content.

Font styles to use
Serif
Sans Serif

Requirements
Must have
• all information provided on separate sheet
Should not have
• Additional information that may clogg up design

```html
<!DOCTYPE html>
<html lang="en">
<head>
<meta charset="utf-8">
<title>Flue Guardian – Business Card</title>
<link rel="stylesheet" href="https://fonts.googleapis.com/css2?family=Cinzel:wght@400;500&family=Questrial&display=swap">
<style>
  :root {
    --page-bg: #e9e6e1;
    --card-bg: #ffffff;
    --ink: #3a3a3a;
    --ink-soft: #555555;
    --accent: #b4262c;
    --rule: #4a4a4a;
    --flame-tint: #f1e6e6;
  }
  * { box-sizing: border-box; margin: 0; padding: 0; }
  html, body {
    width: 1200px; height: 1022px; overflow: hidden;
    background: var(--page-bg);
  }
  .stage {
    width: 1200px; height: 1022px;
    display: flex; align-items: center; justify-content: center;
  }
  .card {
    position: relative;
    width: 900px; height: 515px;
    background: var(--card-bg);
    box-shadow: 0 10px 30px rgba(0,0,0,.12);
    overflow: hidden;
    color: var(--ink);
  }
  .card__backdrop {
    position: absolute; left: 0; bottom: 0;
    width: 520px; height: 300px;
    background: radial-gradient(ellipse at 35% 75%, var(--flame-tint) 0%, rgba(241,230,230,0) 70%);
  }
  .brand {
    position: absolute; left: 60px; top: 70px;
    display: flex; align-items: center; gap: 24px;
  }
  .brand__mark {
    width: 88px; height: 88px; flex: none;
    border: 7px solid var(--ink-soft);
  }
  .brand__name {
    font-family: "Cinzel", serif; font-weight: 400;
    font-size: 40px; letter-spacing: 2px; line-height: 1;
    color: var(--ink); white-space: nowrap;
    padding-bottom: 14px;
    border-bottom: 2px solid var(--rule);
  }
  .brand__since {
    position: absolute; left: 172px; top: 172px;
    display: flex; align-items: center; gap: 14px;
    font-family: "Cinzel", serif; font-size: 20px; letter-spacing: 2px;
    color: var(--ink-soft);
  }
  .brand__since::after {
    content: ""; width: 140px; height: 2px; background: var(--rule);
  }
  .contact {
    position: absolute; right: 60px; top: 150px;
    list-style: none; text-align: right;
    font-family: "Questrial", sans-serif; font-size: 18px;
    color: var(--ink-soft); line-height: 32px;
  }
  .contact__icons {
    display: flex; justify-content: flex-end; gap: 8px; margin-bottom: 6px;
  }
  .contact__icon { width: 22px; height: 22px; flex: none; }
  .divider {
    position: absolute; left: 60px; top: 262px;
    width: 300px; height: 2px; background: var(--rule);
  }
  .divider--edge {
    left: 0; top: auto; bottom: 34px; width: 900px; height: 2px;
  }
  .services {
    position: absolute; left: 60px; top: 292px;
    list-style: none;
    font-family: "Cinzel", serif; font-size: 19px; letter-spacing: 1px;
    line-height: 32px; color: var(--ink-soft);
  }
  .services__item::before {
    content: ""; display: inline-block;
    width: 8px; height: 8px; border-radius: 50%;
    background: var(--accent); margin-right: 12px; vertical-align: 3px;
  }
  .services__item--inline { margin-left: 14px; }
</style>
</head>
<body>
<main class="stage">
  <article class="card">
    <div class="card__backdrop" role="img" aria-label="Faint flame decoration area"></div>

    <header class="brand">
      <span class="brand__mark" aria-hidden="true"></span>
      <h1 class="brand__name">Flue Guardian</h1>
    </header>
    <p class="brand__since">Inc 1989</p>

    <div class="contact">
      <div class="contact__icons" aria-hidden="true">
        <svg class="contact__icon" viewBox="0 0 20 20"><circle cx="10" cy="10" r="10" fill="#b4262c"/><path d="M6.5 5.5l2 0 1 2.5-1.3 1a6 6 0 0 0 2.8 2.8l1-1.3 2.5 1v2a1 1 0 0 1-1 1A8.5 8.5 0 0 1 5.5 6.5a1 1 0 0 1 1-1z" fill="#fff"/></svg>
        <svg class="contact__icon" viewBox="0 0 20 20"><circle cx="10" cy="10" r="10" fill="#b4262c"/><circle cx="10" cy="10" r="5" fill="none" stroke="#fff" stroke-width="1.2"/><path d="M5 10h10M10 5c-2.5 3-2.5 7 0 10M10 5c2.5 3 2.5 7 0 10" fill="none" stroke="#fff" stroke-width="1"/></svg>
        <svg class="contact__icon" viewBox="0 0 20 20"><circle cx="10" cy="10" r="10" fill="#b4262c"/><rect x="5" y="6.5" width="10" height="7" fill="none" stroke="#fff" stroke-width="1.3"/><path d="M5 6.5l5 4 5-4" fill="none" stroke="#fff" stroke-width="1.3"/></svg>
      </div>
      <p>802-555-0147</p>
      <p>info@flueguardianvt.example</p>
      <p>www.flueguardianvt.example</p>
    </div>

    <div class="divider" aria-hidden="true"></div>

    <ul class="services">
      <li><span class="services__item">Full Masonry Services</span></li>
      <li><span class="services__item">Historic Chimney Restoration</span></li>
      <li><span class="services__item">Stainless Steel Liners</span></li>
      <li><span class="services__item">ACSB Certified Chimney Sweep</span></li>
      <li><span class="services__item">Fully Insured</span><span class="services__item services__item--inline">Free Estimates</span></li>
    </ul>

    <div class="divider divider--edge" aria-hidden="true"></div>
  </article>
</main>
</body>
</html>
```